uk based ecommerce website requires fresh look ,high quality look and feel

we are a web based company selling eco friendly ground reinforcement grids to diy and construction sectors
our existing website is www.pondermeshpaths.co.uk ,

we have already updated the logo so that is the branding sorted .so we need a ecommerce website that is very much up-to date in design and layout and which has content management system for ease of use so that we can add products and information as required.

Use current logo as reference for colour scheme.
www.pondermeshpaths.co.uk

The current website has 6 pages accessible through the navigation bar, I would now like 5 pages, removing the need for the Trade Enquiries page possibly have it with along with contact us.

Target Market(s)

construction industry , diy end users,
retail market, landscapers, gardeners

Industry/Entity Type

Construction

Font styles to use
Other font styles liked:
• logo font prometo

Colors
f78f20
9bcb3c

Requirements
Must have
• logo colours and logo design in website with cms responsive design for tablet and mobile devices
• expect content to work flawlessly and look great across all devices
• HTML 5 custom design with coding as required
• must have good experiance in ecommerce website design
• eye catching, high quality look and feel and very user friedly ,very up-to date.
Nice to have
• picture slider show
• explain in writing what exactly i am getting in my ecommerce website
Should not have
• plain , basic design , old fashion looking ,cheap look

```html
<!DOCTYPE html>
<html lang="en">
<head>
<meta charset="utf-8">
<title>Pondermesh Ground Solutions – Gravel Driveways</title>
<link href="https://fonts.googleapis.com/css2?family=Open+Sans:wght@400;600;700&family=Orbitron:wght@700&display=swap" rel="stylesheet">
<style>
:root{
  --orange:#f78f20;
  --orange-dark:#e07a12;
  --green:#9bcb3c;
  --green-dark:#6fa421;
  --page-green:#6fae2c;
  --text:#666;
  --dark:#333;
  --footer:#353535;
  --footer-text:#e8e8e8;
  --white:#fff;
}
*{box-sizing:border-box;margin:0;padding:0}
html,body{width:1054px;height:1200px;overflow:hidden}
body{background:var(--page-green);font-family:"Open Sans",Arial,sans-serif;color:var(--text);position:relative}
.page{position:absolute;left:58px;top:0;width:937px;height:1200px;background:var(--white)}
.abs{position:absolute}

/* top bar */
.top-bar{left:0;top:0;width:937px;height:22px;background:var(--orange);display:flex;justify-content:flex-end;align-items:center;padding-right:30px;font-size:8px;color:var(--white)}
.top-bar a{color:var(--white);text-decoration:none}
.top-bar .sep{margin:0 22px}

/* header */
.brand{left:28px;top:46px;display:flex;align-items:center;gap:8px}
.brand-mark{width:22px;height:22px;border-radius:50%;background:var(--green)}
.brand-name{font-size:19px;font-weight:700;color:var(--orange);letter-spacing:.3px}
.search{left:564px;top:54px;width:202px;height:23px;border:1px solid #ccc;display:flex}
.search span{flex:1;font-size:8px;color:#888;padding:6px 8px}
.search b{width:50px;background:var(--green);color:var(--white);font-size:8px;font-weight:400;display:flex;align-items:center;justify-content:center;margin:2px}
.cart{left:782px;top:54px;width:127px;height:23px;border:1px solid #ccc;font-size:8px;color:#555;display:flex;align-items:center;justify-content:center;gap:5px}
.cart em{font-style:normal;color:var(--orange)}

/* nav */
.nav{left:20px;top:109px;width:889px;height:41px}
.nav-products{position:absolute;left:0;top:0}
.nav-bar{position:absolute;left:190px;top:0;width:699px;height:41px;background:var(--orange);display:flex;align-items:center;font-size:12px;color:var(--white);font-weight:600}
.nav-bar span{height:41px;display:flex;align-items:center;padding:0 23px;border-right:1px solid var(--orange-dark)}
.nav-bar span:last-child{border:0}
.nav-label{position:absolute;left:50px;top:12px;color:var(--white);font-size:13px;font-weight:700}

/* sidebar */
.side-menu{left:28px;top:164px;width:180px;list-style:none}
.side-menu li{height:36.8px;background:var(--orange);border-bottom:1px solid var(--orange-dark);color:var(--white);font-size:9.5px;font-weight:600;padding:0 14px;display:flex;align-items:center}
.side-menu li.active{background:var(--green-dark)}

/* slider */
.hero{left:224px;top:164px;width:684px;height:368px;background:linear-gradient(135deg,#4f8a25 0%,#6fa83a 30%,#9a9a94 45%,#6fa83a 60%,#7a5a4a 85%,#6b4a3b 100%)}
.hero-title{left:30px;top:124px;font-family:"Orbitron",sans-serif;font-size:25px;color:var(--white);letter-spacing:1px}
.hero-sub{left:31px;top:160px;font-size:12px;font-weight:700;color:var(--white)}
.hero-text{left:33px;top:181px;width:280px;font-size:10px;line-height:19px;color:var(--white)}
.hero-btn{left:32px;top:229px;width:124px;height:38px;background:var(--green);color:var(--white);font-size:11px;font-weight:700;display:flex;align-items:center;justify-content:center}
.hero-arrows{left:670px;top:461px;display:flex;gap:2px}
.hero-arrows span{width:21px;height:20px;background:var(--orange);display:flex;align-items:center;justify-content:center}

/* content */
.section-title{left:28px;top:571px;font-family:"Orbitron",sans-serif;font-size:17px;color:var(--orange);letter-spacing:.5px}
.intro{left:28px;top:602px;width:480px;font-size:11px;line-height:25.6px}
.intro p{margin-bottom:8px}
.hex-photo{top:590px;width:146px;height:164px}
.enquiry{left:580px;top:790px;width:300px;text-align:center;font-size:10.5px;color:var(--orange);line-height:21px;font-weight:600}
.enquiry-text{left:580px;top:837px;width:300px;text-align:center;font-size:11px;line-height:25.6px}

/* footer */
.footer{left:0;top:956px;width:937px;height:198px;background:var(--footer);color:var(--footer-text)}
.footer h3{position:absolute;top:22px;font-size:11.5px;font-weight:600;color:var(--green);padding-bottom:7px;border-bottom:1px solid #555}
.links{position:absolute;left:52px;top:50px;list-style:none;font-size:9.5px}
.links li{height:19.4px;display:flex;align-items:center;gap:10px}
.links li::before{content:"";width:4px;height:4px;border-radius:50%;background:var(--footer-text)}
.links li.on{color:var(--green)}
.contact{position:absolute;left:204px;top:52px;font-size:9.5px;line-height:17px}
.contact .row{display:flex;gap:9px;margin-bottom:9px}
.contact .big{font-size:11.5px;color:var(--white)}
.testimonial{position:absolute;left:451px;top:52px;width:200px;font-size:9.5px;line-height:16.5px}
.quote{text-align:center;font-size:22px;color:#bbb;height:20px;line-height:22px}
.social{position:absolute;left:700px;top:63px;display:grid;grid-template-columns:101px 90px;row-gap:18px;font-size:11px}
.social span{display:flex;align-items:center;gap:10px}
.social i{width:22px;height:22px;border-radius:50%;display:block}
.cards{position:absolute;left:704px;top:150px;display:flex;gap:5px}
.cards span{width:33px;height:20px;background:var(--white);border-radius:2px;color:#333;font-size:6px;font-weight:700;display:flex;align-items:center;justify-content:center}
.copyright{left:0;top:1154px;width:937px;height:46px;background:var(--orange);color:var(--white);font-size:10px;display:flex;align-items:center;justify-content:center}
</style>
</head>
<body>
<div class="page">
  <div class="abs top-bar"><a>HOME</a><span class="sep">|</span><a>MY ACCOUNT</a><span class="sep">|</span><a>LOGIN</a><span class="sep">|</span><a>REGISTER</a></div>

  <div class="abs brand"><span class="brand-mark"></span><span class="brand-name">Pondermesh</span></div>
  <div class="abs search"><span>SEARCH YOUR ITEMS :</span><b>SEARCH</b></div>
  <div class="abs cart">
    <svg width="9" height="8" viewBox="0 0 9 8"><path d="M0 1h2l1 4h5l1-3H3" fill="none" stroke="#f78f20" stroke-width="1.2"/><circle cx="3.5" cy="7" r=".8" fill="#f78f20"/><circle cx="7" cy="7" r=".8" fill="#f78f20"/></svg>
    YOUR CART IS : <em>0 ITEMS</em>
  </div>

  <nav class="abs nav">
    <svg class="nav-products" width="200" height="41" viewBox="0 0 200 41"><polygon points="0,20.5 12,0 186,0 198,20.5 186,41 12,41" fill="#7fb92e"/></svg>
    <span class="nav-label">PRODUCTS &nbsp;&nbsp;&nbsp;&nbsp;⌄</span>
    <div class="nav-bar"><span>SHOP</span><span style="padding:0 32px 0 35px">ABOUT US</span><span>GROUND SOLUTIONS</span><span style="padding:0 33px 0 27px">PONDERMESH</span><span>CONTACT US</span></div>
  </nav>

  <ul class="abs side-menu">
    <li>GEOTEXTILE MEMBRANES</li>
    <li class="active">LIGHT DOMESTIC DRIVEWAYS</li>
    <li>HEAVY DOMESTIC DRIVEWAYS</li>
    <li>PARKING AND PATHWAY SYSTEM</li>
    <li>GRASS REINFORCEMENT MESH &amp;</li>
    <li>TURF REINFORCEMENT MESH</li>
    <li>STEEL U PINS</li>
    <li>COMMERCIAL PARKING SYSTEM</li>
    <li>TERRALOCK GRID</li>
    <li>MONTHLY SPECIALS</li>
  </ul>

  <div class="abs hero" role="img" aria-label="Aerial view of a curving gravel path through lawn beside a timber deck">
    <div class="abs hero-title">PONDERMESH ECO</div>
    <div class="abs hero-sub">SOLUTIONS LTD STABILISED GRAVEL</div>
    <div class="abs hero-text">Part of a natural porous paving system, when filled with gravel this gives you an eco-friendly</div>
    <div class="abs hero-btn">VIEW PRODUCT</div>
  </div>
  <div class="abs hero-arrows">
    <span><svg width="6" height="10"><path d="M5 1L1 5l4 4" fill="none" stroke="#fff" stroke-width="1.3"/></svg></span>
    <span><svg width="6" height="10"><path d="M1 1l4 4-4 4" fill="none" stroke="#fff" stroke-width="1.3"/></svg></span>
  </div>

  <h2 class="abs section-title">GRAVEL DRIVEWAYS</h2>
  <div class="abs intro">
    <p>Gravel driveways are one of the most popular choices for driveways and hard landscaping in the UK and it's easy to see why. It's cost effective, low maintenance and looks great particularly in rural settings or in town where it matches the predominant stone and brick</p>
    <p>There is an immense choice of size, colours and shapes available, making it an excellent choice for resurfacing. Gravel is also a very good deterrent against any kind of burglary as it makes a crunching noise as you walk over the surface, making it not a favorite amongst the undesirables of our society.</p>
    <p>The combination of gravel and our Cellular ground reinforcement grid system's makes the perfect choice for the modern driveway or path, Incorporating the tried and tested gravel driveway and combining with the holding chambers of the ground reinforcement system. This will not be moving around like the normal gravel driveway which makes it the perfect choice. This system does not require planning permission as it is free draining</p>
  </div>

  <svg class="abs hex-photo" style="left:566px" viewBox="0 0 146 164" role="img" aria-label="Car wheel resting on a gravel driveway">
    <defs><linearGradient id="g1" x1="0" y1="0" x2="1" y2="1"><stop offset="0" stop-color="#3a3a3a"/><stop offset=".5" stop-color="#8a8a8a"/><stop offset="1" stop-color="#bdbdbd"/></linearGradient></defs>
    <polygon points="73,3 142,41 142,123 73,161 4,123 4,41" fill="none" stroke="#f78f20" stroke-width="2"/>
    <polygon points="73,10 136,45 136,119 73,154 10,119 10,45" fill="url(#g1)"/>
  </svg>
  <svg class="abs hex-photo" style="left:748px" viewBox="0 0 146 164" role="img" aria-label="Brick house with gravel drive and garden trees">
    <defs><linearGradient id="g2" x1="0" y1="0" x2="0" y2="1"><stop offset="0" stop-color="#5d7a3a"/><stop offset=".55" stop-color="#5a4a42"/><stop offset="1" stop-color="#a8a8a2"/></linearGradient></defs>
    <polygon points="73,3 142,41 142,123 73,161 4,123 4,41" fill="none" stroke="#f78f20" stroke-width="2"/>
    <polygon points="73,10 136,45 136,119 73,154 10,119 10,45" fill="url(#g2)"/>
  </svg>

  <div class="abs enquiry">ALL ENQUIRIES BY EMAIL ON &nbsp;OUR CONTACT PAGE<br>OR BY CALLING ON : 0845-555-0199</div>
  <div class="abs enquiry-text">Our If you feel this is the best choice for you then go to our online store and buy with confidence because this is a light-weight eco-friendly and which is easy</div>

  <footer class="abs footer">
    <h3 style="left:52px;width:124px">QUICK LINKS</h3>
    <ul class="links">
      <li>Shop</li><li class="on">About us</li><li>Ground Solutions</li><li>Pondermesh</li><li>Customer Services</li><li>Request a Quote</li><li>Contact Us</li>
    </ul>

    <h3 style="left:204px;width:194px">CONTACT INFO</h3>
    <div class="contact">
      <div class="row"><svg width="9" height="10" viewBox="0 0 9 10" style="margin-top:4px"><path d="M1 1c0 4 3 8 7 8l1-2-2-1-1 1C4 6 3 5 3 4l1-1-1-2z" fill="#f78f20"/></svg><div><span class="big">0138-555-0142 | 0845-555-0173</span><br>24 Hour Messaging Service</div></div>
      <div class="row"><svg width="9" height="11" viewBox="0 0 9 11" style="margin-top:3px"><path d="M4.5 0A4 4 0 0 0 .5 4c0 3 4 7 4 7s4-4 4-7a4 4 0 0 0-4-4z" fill="#f78f20"/><circle cx="4.5" cy="4" r="1.5" fill="#353535"/></svg><div>Harrowfield House,Alder Park Ind Est,<br>Westbury GX1 2AB</div></div>
      <div class="row"><svg width="11" height="10" viewBox="0 0 11 10" style="margin-top:3px"><path d="M0 5L11 0 8 10 5 6z" fill="#f78f20"/></svg><div>sales@pondermeshpaths.co.uk<br>Mon to Fri-9.00am to 6.00pm</div></div>
    </div>

    <h3 style="left:451px;width:198px">TESTIMONIALS</h3>
    <div class="testimonial">
      <div class="quote">“</div>
      <p style="margin-top:4px">Quality products at an affordable price and which meets the requirements of our customers. We supply a permeable paving system that keeps the traditional</p>
      <p style="margin-top:8px;font-size:10.5px"><b style="color:#fff;font-weight:600">Tam Redford</b>,Manager<br>Brookline Landscapes</p>
    </div>

    <h3 style="left:700px;width:207px">FOLLOW US</h3>
    <div class="social">
      <span><i style="background:var(--orange)"></i>Folkspace</span>
      <span><i style="background:var(--green)"></i>Chirper</span>
      <span><i style="background:var(--orange)"></i>Pinboardly</span>
      <span><i style="background:var(--orange)"></i>Circlenet</span>
    </div>
    <div class="cards"><span>CardOne</span><span>Findcard</span><span>PayPath</span><span>AmeriPay</span><span>Vista</span></div>
  </footer>

  <div class="abs copyright">©2016. PONDERMESHPATHS. ALL RIGHTS RESERVED.</div>
</div>
</body>
</html>
```